I need to make a car magnet

It needs to include the words "PLAVO TOUR" and "2026 MEMBER" as well as the attached silhouette of the golfer. The color scheme needs to be navy, red and white. The shape and dimensions are open for interpretation

```html
<!DOCTYPE html>
<html lang="en">
<head>
<meta charset="utf-8">
<title>PLAVO TOUR – Car Magnet</title>
<link rel="stylesheet" href="https://fonts.googleapis.com/css2?family=Russo+One&display=swap">
<style>
  :root {
    --navy: #1f2d5e;
    --navy-light: #34447a;
    --red: #e42332;
    --white: #ffffff;
    --backdrop: #b3b3b3;
  }
  html, body {
    margin: 0;
    padding: 0;
    width: 892px;
    height: 1200px;
    overflow: hidden;
    background: var(--backdrop);
  }
  .magnet {
    position: absolute;
    left: 36px;
    top: 395px;
    width: 820px;
    height: 409px;
    background: radial-gradient(ellipse at 50% 45%, var(--navy-light) 0%, var(--navy) 62%);
    box-shadow: 2px 3px 5px rgba(0,0,0,0.3);
    overflow: hidden;
    font-family: "Russo One", sans-serif;
  }
  .golfer {
    position: absolute;
    top: 29px;
    width: 190px;
    height: 372px;
    border-radius: 60px 60px 8px 8px;
  }
  .golfer--left { left: 9px; background: var(--red); }
  .golfer--right { left: 620px; background: var(--white); }
  .title {
    position: absolute;
    left: 0;
    width: 820px;
    margin: 0;
    text-align: center;
    line-height: 1;
    font-weight: 400;
    transform: skewX(-12deg);
  }
  .title--name {
    top: 80px;
    font-size: 96px;
    color: var(--red);
    letter-spacing: 2px;
  }
  .title--tour {
    top: 164px;
    font-size: 90px;
    color: var(--white);
  }
  .member-badge {
    position: absolute;
    left: 236px;
    top: 287px;
    width: 348px;
    height: 45px;
    background: var(--red);
    transform: skewX(-10deg);
    display: flex;
    align-items: center;
    justify-content: center;
    color: var(--white);
    font-size: 31px;
    letter-spacing: 1px;
  }
</style>
</head>
<body>
  <div class="magnet">
    <div class="golfer golfer--left" role="img" aria-label="Red silhouette of a golfer putting, facing right"></div>
    <div class="golfer golfer--right" role="img" aria-label="White silhouette of a golfer putting, facing left"></div>
    <h1 class="title title--name">PLAVO</h1>
    <h2 class="title title--tour">TOUR</h2>
    <div class="member-badge">2026 MEMBER</div>
  </div>
</body>
</html>
```